We need a complete design for our construction company KELTO CONSTRUCTION based in Auckland New Zealand, we need a logo, website, business card, vehicle design etc..
We are a mid to high-end construction company who work mostly on residential projects and some commercial.

What we want to see in the design;
Professional,
Architectural,
Simple,
Alternative,

We want the design to communicate professionalism, high quality wormanship and and quality service.

Target Market(s)

People looking for a quality building/ construction company

Industry/Entity Type

Construction Company

Contact Information for Business Card

KELTO CONSTRUCTION.co.nz
Lino Verasek
lino@keltoconstruction.example.nz
021 5807 462

Logo Text

KELTO CONSTRUCTION

Number of Pages Required

5+ page

Font styles to use
Sans Serif

Colors

Designer to choose colors to be used in the design.

Requirements
Must have
• Must appear high end, professional, quality, be simple, easy to use, give security to potential clients
Nice to have
• high-quality photos of our recent projects
• about us page
• blog page
• contact us page
• high quality content
Should not have
• should not be hard to use and have too much going on.

```html
<!DOCTYPE html>
<html lang="en">
<head>
<meta charset="utf-8">
<title>KELTO CONSTRUCTION</title>
<link rel="stylesheet" href="https://fonts.googleapis.com/css2?family=Poppins:wght@300;400;500&family=Raleway:wght@800;900&family=Lato:ital,wght@0,700;1,400&display=swap">
<style>
:root{
  --gold:#b38b3c;
  --ink:#111111;
  --text:#555555;
  --dark:#16161c;
  --white:#ffffff;
  --line:#3a3a42;
  --muted:#a9a9a9;
}
*{margin:0;padding:0;box-sizing:border-box}
html,body{width:1200px;height:2655px;overflow:hidden;background:var(--white)}
body{position:relative;font-family:"Poppins",sans-serif;color:var(--text)}
.abs{position:absolute}

/* header */
.site-header{left:0;top:0;width:1200px;height:104px;background:rgba(40,38,36,.74);z-index:2}
.brand{left:80px;top:36px;font-weight:400;font-size:21px;letter-spacing:4px;color:var(--gold)}
.main-nav{top:40px;left:0;width:1200px;height:24px}
.main-nav a{position:absolute;font-size:15px;color:#e6e6e6;text-decoration:none;letter-spacing:.3px}
.main-nav a.active{color:var(--white)}

/* hero */
.hero{left:0;top:0;width:1200px;height:713px;
  background:
    radial-gradient(ellipse 380px 260px at 820px 260px,rgba(255,255,255,.55),rgba(255,255,255,0) 70%),
    radial-gradient(ellipse 260px 90px at 530px 560px,rgba(235,130,40,.35),rgba(235,130,40,0) 70%),
    linear-gradient(180deg,#dcd9d4 0%,#d0cbc4 45%,#bfb9b1 75%,#a9a39b 100%)}
.hero-title{left:0;top:355px;width:1200px;text-align:center;font-family:"Raleway",sans-serif;font-weight:800;font-size:50px;color:var(--ink);letter-spacing:.5px}
.hero-sub{left:380px;top:424px;width:440px;text-align:center;font-weight:500;font-size:15px;line-height:23px;color:var(--ink)}
.btn-explore{left:513px;top:499px;width:174px;height:44px;background:var(--gold);border:1px solid #7d6026;color:var(--white);font-size:17px;line-height:42px;text-align:center}

/* about */
.about{left:0;top:713px;width:1200px;height:333px;background:linear-gradient(180deg,#ffffff,#f3f3f3)}
.section-title{left:0;width:1200px;text-align:center;font-family:"Raleway",sans-serif;font-weight:900;font-size:42px;color:var(--gold)}
.about-copy{left:150px;width:900px;text-align:center;font-size:14.5px;line-height:23px;color:#666}

/* work */
.work-band{left:0;top:1046px;width:1200px;height:106px;background:linear-gradient(180deg,#0e0e12,#23232a)}
.gallery{left:0;top:1152px;width:1200px;height:678px;background:#222}
.tile{position:absolute;box-shadow:inset 0 0 0 1px rgba(255,255,255,.08)}
.feature-overlay{left:545px;top:1152px;width:597px;height:338px;background:rgba(50,45,36,.45)}
.feature-title{left:545px;top:1252px;width:597px;text-align:center;font-family:"Lato",sans-serif;font-weight:700;font-size:21px;color:var(--white)}
.feature-sub{left:545px;top:1282px;width:597px;text-align:center;font-size:16px;color:#f0f0f0}

/* blog */
.blog{left:0;top:1830px;width:1200px;height:577px;background:var(--white)}
.blog-backdrop{left:0;top:2150px;width:1200px;height:257px;background:linear-gradient(180deg,rgba(255,255,255,0) 0%,#e4e6e8 55%,#c3c7cc 100%)}
.card{position:absolute;top:1973px;width:312px;height:313px}
.card-photo{position:absolute;left:0;top:0;width:312px;height:313px}
.card-caption{position:absolute;left:0;bottom:0;width:312px;height:62px;background:rgba(10,10,10,.9)}
.card.featured .card-caption{background:rgba(179,139,60,.94)}
.date{position:absolute;left:38px;top:-28px;width:57px;height:57px;border-radius:50%;border:2px solid var(--white);color:var(--white);text-align:center}
.date .day{display:block;font-size:21px;line-height:24px;margin-top:5px}
.date .mon{display:block;font-size:12px;line-height:14px}
.card-title{position:absolute;left:110px;top:4px;font-family:"Lato",sans-serif;font-weight:700;font-size:21px;color:var(--white)}
.card-sub{position:absolute;left:110px;top:33px;font-family:"Lato",sans-serif;font-style:italic;font-size:13.5px;color:#eee}

/* footer */
.site-footer{left:0;top:2404px;width:1200px;height:251px;background:linear-gradient(180deg,#1a1a22,#0f0f14)}
.footer-head{top:2476px;font-family:"Raleway",sans-serif;font-weight:800;font-size:22px;color:var(--gold)}
.divider{top:2470px;width:1px;height:110px;background:var(--line)}
.social{top:2520px;width:42px;height:42px;border:1px solid #bbb;color:var(--white);font-size:11px;font-weight:500;line-height:40px;text-align:center}
.email-field{left:421px;top:2520px;width:331px;height:38px;border-radius:19px;background:#3b3b42;color:var(--muted);font-size:17px;line-height:38px;padding-left:24px}
.contact-line{left:850px;font-size:14.5px;color:#aaa}
.copyright{left:0;top:2599px;width:1200px;text-align:center;font-size:14px;color:#ddd}
</style>
</head>
<body>

<section class="hero abs" role="img" aria-label="Bright modern living room with white sofas, fireplace and sea view windows"></section>

<header class="site-header abs">
  <div class="brand abs">KELTO CONSTRUCTION</div>
  <nav class="main-nav abs">
    <a class="active" style="left:579px">HOME</a>
    <a style="left:673px">ABOUT US</a>
    <a style="left:798px">PROJECTS</a>
    <a style="left:924px">BLOGS</a>
    <a style="left:1021px">CONTACT US</a>
  </nav>
</header>

<h1 class="hero-title abs">KELTO CONSTRUCTION</h1>
<p class="hero-sub abs">Lorem Ipsum is simply dummy text of the printing and typesetting industry Lorem Ipsum has.</p>
<div class="btn-explore abs">EXPLORE MORE</div>

<section class="about abs"></section>
<h2 class="section-title abs" style="top:780px">ABOUT US</h2>
<p class="about-copy abs" style="top:846px">Lorem Ipsum is simply dummy text of the printing and typesetting industry. Lorem Ipsum has been the industry's standard dummy text ever since the 1500s, when an unknown printer took a galley of type and scrambled it to make a type specimen book. It has survived not only five centuries, but also the leap into electronic typesetting.</p>
<p class="about-copy abs" style="top:938px">Lorem Ipsum is simply dummy text of the printing and typesetting industry. Lorem Ipsum has been the industry's standard dummy text ever since the 1500s, when an unknown printer took...</p>

<section class="work-band abs"></section>
<h2 class="section-title abs" style="top:1072px">OUR WORK</h2>

<div class="gallery abs">
  <div class="tile" style="left:0;top:0;width:209px;height:169px;background:linear-gradient(180deg,#d6dde4 0%,#c2cbd3 35%,#3f3a36 36%,#5a5048 80%,#7c8a5a 100%)" role="img" aria-label="Dark timber modern house"></div>
  <div class="tile" style="left:0;top:169px;width:209px;height:169px;background:linear-gradient(180deg,#3d79b8 0%,#8fb3d6 50%,#eef1f3 70%,#cfd6dc 100%)" role="img" aria-label="Curved white architectural building"></div>
  <div class="tile" style="left:209px;top:0;width:336px;height:338px;background:linear-gradient(160deg,#eef3f7 0%,#b9c8d4 40%,#5f7585 70%,#2e3a44 100%)" role="img" aria-label="Glass and steel facade detail"></div>
  <div class="tile" style="left:545px;top:0;width:597px;height:338px;background:linear-gradient(100deg,#cbbfae 0%,#a89880 45%,#6e604c 75%,#3f372b 100%)" role="img" aria-label="Construction worker in hard hat on site"></div>
  <div class="tile" style="left:1142px;top:0;width:58px;height:169px;background:linear-gradient(180deg,#e6e9eb,#a3abb2)" role="img" aria-label="White modern building"></div>
  <div class="tile" style="left:1142px;top:169px;width:58px;height:169px;background:linear-gradient(180deg,#d0bca0,#6d5a44)" role="img" aria-label="Builder at work"></div>
  <div class="tile" style="left:0;top:338px;width:545px;height:340px;background:linear-gradient(180deg,#3270b4 0%,#6f9dcc 40%,#a9b6c0 62%,#6f757a 85%,#4a5a3c 100%)" role="img" aria-label="Curving modern museum building with glass front"></div>
  <div class="tile" style="left:545px;top:338px;width:336px;height:340px;background:linear-gradient(180deg,#3a4b6a 0%,#2a3246 45%,#1d1f26 75%,#4a3a22 100%)" role="img" aria-label="Wavy tower at dusk"></div>
  <div class="tile" style="left:881px;top:338px;width:261px;height:169px;background:linear-gradient(180deg,#b4cfe6 0%,#9fb8cc 50%,#5f6b72 100%)" role="img" aria-label="Engineer with tablet on site"></div>
  <div class="tile" style="left:881px;top:507px;width:261px;height:171px;background:linear-gradient(180deg,#4a7eab 0%,#1f3a52 60%,#8a6330 85%,#2c3b2a 100%)" role="img" aria-label="Stacked modern house lit at night"></div>
  <div class="tile" style="left:1142px;top:338px;width:58px;height:340px;background:linear-gradient(180deg,#55636f,#2a2f36)" role="img" aria-label="Office towers"></div>
</div>
<div class="feature-overlay abs"></div>
<svg class="abs" style="left:580px;top:1151px" width="40" height="20" viewBox="0 0 40 20"><polygon points="0,0 40,0 20,20" fill="#23232a"/></svg>
<div class="feature-title abs">LOREM IPSUM IS SIMPLY DUMMY</div>
<div class="feature-sub abs">Lorem Ipsum is simply dummy text of the printing</div>
<svg class="abs" style="left:822px;top:1341px" width="44" height="44" viewBox="0 0 44 44"><circle cx="22" cy="22" r="20" fill="none" stroke="#fff" stroke-width="2"/><polygon points="18,14 30,22 18,30" fill="#fff"/></svg>
<svg class="abs" style="left:17px;top:1469px" width="44" height="44" viewBox="0 0 44 44"><circle cx="22" cy="22" r="20" fill="none" stroke="#fff" stroke-width="2"/><polyline points="25,15 18,22 25,29" fill="none" stroke="#fff" stroke-width="2.5"/></svg>
<svg class="abs" style="left:1138px;top:1469px" width="44" height="44" viewBox="0 0 44 44"><circle cx="22" cy="22" r="20" fill="none" stroke="#fff" stroke-width="2"/><polyline points="19,15 26,22 19,29" fill="none" stroke="#fff" stroke-width="2.5"/></svg>

<section class="blog abs"></section>
<div class="blog-backdrop abs" role="img" aria-label="Faint sweeping white modern building along the lower edge"></div>
<h2 class="section-title abs" style="top:1880px">RECENTLY BLOG POSTED</h2>

<article class="card" style="left:88px">
  <div class="card-photo" style="background:linear-gradient(160deg,#5f97d0 0%,#e4edf3 40%,#7f9bb0 65%,#3f5a3a 100%)" role="img" aria-label="Glass towers with sun flare"></div>
  <div class="card-caption">
    <div class="date"><span class="day">05</span><span class="mon">Feb</span></div>
    <div class="card-title">Lorem ipsum text.</div>
    <div class="card-sub">Lorem ipsum is simply dummy</div>
  </div>
</article>
<article class="card featured" style="left:444px">
  <div class="card-photo" style="background:linear-gradient(180deg,#5a8cc3 0%,#a9bfd2 45%,#c9b48e 70%,#6b6250 100%)" role="img" aria-label="City skyline from a walkway at sunset"></div>
  <div class="card-caption">
    <div class="date"><span class="day">05</span><span class="mon">Feb</span></div>
    <div class="card-title">Lorem ipsum text.</div>
    <div class="card-sub">Lorem ipsum is simply dummy</div>
  </div>
</article>
<article class="card" style="left:801px">
  <div class="card-photo" style="background:linear-gradient(180deg,#5fa2dc 0%,#b7d2e6 35%,#4f7896 60%,#c9cdd0 100%)" role="img" aria-label="Modern glass office building"></div>
  <div class="card-caption">
    <div class="date"><span class="day">05</span><span class="mon">Feb</span></div>
    <div class="card-title">Lorem ipsum text.</div>
    <div class="card-sub">Lorem ipsum is simply dummy</div>
  </div>
</article>

<footer class="site-footer abs"></footer>
<h3 class="footer-head abs" style="left:80px">CONNECT</h3>
<div class="social abs" style="left:76px">Kin</div>
<div class="social abs" style="left:126px">Pix</div>
<div class="social abs" style="left:176px">Orb</div>
<div class="divider abs" style="left:384px"></div>
<h3 class="footer-head abs" style="left:421px">SIGN UP AND RECEIVE UPDATES!</h3>
<div class="email-field abs">Enter Email</div>
<div class="divider abs" style="left:818px"></div>
<h3 class="footer-head abs" style="left:850px">CONTACT US</h3>
<p class="contact-line abs" style="top:2517px">123 Building Name, City, Country - Zipcode</p>
<p class="contact-line abs" style="top:2540px">123-4567-890</p>
<p class="copyright abs">© KELTO Constructions.&nbsp; - 2018 All Right Reserved</p>

</body>
</html>
```